Namibia currently imports 60% of its food. Harvest Crest Oruva is an initiative which will assist Namibia to become self sustainable in terms of food production. We aim to do this through the development of 3 agricultural production zones which will include farming zones, local farmer assistance, processing and distribution of the final products. Please see our project overview attached.

```html
<!DOCTYPE html>
<html lang="en">
<head>
<meta charset="utf-8">
<title>Harvest Crest Oruva</title>
<link rel="stylesheet" href="https://fonts.googleapis.com/css2?family=Noto+Serif:wght@500;700&family=Roboto:wght@400;500;700&display=swap">
<style>
:root{
  --green:#0a6a3a;
  --green-deep:#0d6b3c;
  --tan:#c6a684;
  --tan-dark:#b8946e;
  --ink:#2b2b2b;
  --text:#3d3d3d;
  --white:#ffffff;
  --black:#000000;
  --rule:#5a5a5a;
}
*{box-sizing:border-box;margin:0;padding:0}
html,body{width:1200px;height:4044px;overflow:hidden}
body{position:relative;background:var(--white);font-family:"Roboto",Arial,sans-serif;color:var(--text)}
.abs{position:absolute}
.serif{font-family:"Noto Serif",Georgia,serif}
.btn{position:absolute;display:flex;align-items:center;justify-content:center;border-radius:24px;font-family:"Roboto",Arial,sans-serif;font-weight:700;font-size:14px;color:var(--white);text-transform:uppercase;letter-spacing:.2px}
.btn-green{background:var(--green)}
.btn-tan{background:var(--tan)}

/* header */
.site-header{left:0;top:0;width:1200px;height:96px;background:var(--white)}
.brand{left:113px;top:30px;font-family:"Noto Serif",Georgia,serif;font-size:30px;font-weight:500;color:var(--green);display:flex;align-items:center;gap:10px;white-space:nowrap}
.brand-dot{width:14px;height:14px;border-radius:50%;background:var(--tan)}
.nav{left:521px;top:38px;display:flex;gap:31px;font-size:15px;color:var(--ink)}

/* hero */
.hero-photo{left:0;top:96px;width:1200px;height:800px;background:linear-gradient(180deg,#3f4e34 0%,#55603f 40%,#3b4a30 75%,#2f3a27 100%)}
.hero-welcome{left:0;top:398px;width:1200px;text-align:center;font-size:34px;font-weight:700;color:var(--white)}
.hero-title{left:0;top:448px;width:1200px;text-align:center;font-size:64px;font-weight:700;color:var(--white)}
.wave{position:absolute;left:0;width:1200px}

/* need food */
.section-title{left:0;width:1200px;text-align:center;font-size:34px;font-weight:700}
.need-title{top:978px;color:var(--ink)}
.need-lead{left:188px;top:1032px;width:824px;text-align:center;font-size:14.5px;line-height:29px;color:var(--text)}
.need-body{left:115px;top:1175px;width:481px;text-align:justify;font-size:14.5px;line-height:29px;color:var(--text)}
.need-photo{left:650px;top:1185px;width:435px;height:316px;background:linear-gradient(180deg,#8aa3c0 0%,#9eb0c4 30%,#6e5a44 60%,#5a3f2c 100%)}

/* solution */
.tan-band{left:0;top:1760px;width:1200px;height:383px;background:var(--tan)}
.green-band{left:0;top:2143px;width:1200px;height:589px;background:var(--green-deep)}
.solution-title{top:1826px;color:var(--white)}
.card{position:absolute;top:1908px;width:480px;height:364px;background:var(--white);box-shadow:0 2px 8px rgba(0,0,0,.15)}
.card-photo{position:absolute;left:15px;top:2px;width:450px;height:290px}
.card-label{position:absolute;left:0;top:316px;width:100%;text-align:center;font-size:19px;font-weight:500;color:var(--ink)}
.fish-title{top:2345px;font-size:36px;line-height:49px;color:var(--white)}
.fish-text{left:170px;top:2504px;width:860px;text-align:center;font-size:14.5px;line-height:27px;color:var(--white)}

/* about */
.about-photo{left:119px;top:2818px;width:420px;height:420px;border-radius:50%;border:10px solid var(--green);background:linear-gradient(160deg,#4f7a34 0%,#6f8f45 45%,#3b5b28 100%)}
.about-title{left:596px;top:2818px;font-size:34px;font-weight:700;color:var(--ink)}
.about-text{left:596px;top:2870px;width:487px;font-size:14.5px;line-height:26px;color:var(--text)}

/* footer */
.footer-bg{left:0;top:3400px;width:1200px;height:590px;background:var(--black)}
.news-title{left:102px;top:3602px;font-size:30px;font-weight:700;color:var(--white)}
.news-field{left:558px;top:3597px;width:532px;height:46px;border-radius:24px;background:var(--white);display:flex;align-items:center;padding-left:24px;gap:10px;font-size:13px;color:#777}
.news-btn{left:930px;top:3599px;width:158px;height:42px;font-size:16px}
.rule{left:113px;top:3688px;width:975px;height:1px;background:var(--rule)}
.footer-brand{left:107px;top:3800px;font-family:"Noto Serif",Georgia,serif;font-size:30px;font-weight:500;color:var(--green);display:flex;align-items:center;gap:12px;white-space:nowrap}
.col-title{position:absolute;top:3738px;font-size:13px;font-weight:700;color:var(--white);text-decoration:underline}
.contact-item{position:absolute;left:449px;display:flex;align-items:center;gap:24px;font-size:13.5px;line-height:19px;color:var(--white)}
.icon-ring{width:28px;height:28px;border-radius:50%;border:1px solid #ccc;display:flex;align-items:center;justify-content:center;flex:none}
.links{position:absolute;top:3774px;list-style:none;font-size:13.5px;color:var(--white)}
.links li{height:32px;display:flex;align-items:center;gap:12px}
.copyright{left:0;top:3990px;width:1200px;height:54px;background:var(--tan);display:flex;align-items:center;justify-content:center;font-size:13px;color:var(--white)}
</style>
</head>
<body>

<header class="abs site-header">
  <div class="abs brand"><span>Harvest Crest Oruva</span><span class="brand-dot"></span></div>
  <nav class="abs nav"><span>HOME</span><span>ABOUT US</span><span>SERVICES</span><span>CONTACT US</span></nav>
  <div class="btn btn-green" style="left:928px;top:27px;width:156px;height:43px">Get Started</div>
</header>

<section>
  <div class="abs hero-photo" role="img" aria-label="Young woman tending leafy vegetables in a farm field"></div>
  <div class="abs serif hero-welcome">WELCOME TO</div>
  <h1 class="abs serif hero-title">HARVEST CREST ORUVA</h1>
  <div class="btn btn-tan" style="left:522px;top:555px;width:157px;height:43px">Get Started</div>
  <svg class="wave" style="top:680px" height="240" viewBox="0 0 1200 240" aria-hidden="true">
    <path d="M0,118 C160,8 360,20 620,128 C860,226 1040,210 1200,100 L1200,240 L0,240 Z" fill="#fff"/>
    <path d="M0,118 C160,8 360,20 620,128 C860,226 1040,210 1200,100" fill="none" stroke="#c6a684" stroke-width="10"/>
    <path d="M60,70 C220,-4 400,26 630,112 C850,196 1030,190 1180,98" fill="none" stroke="#0a6a3a" stroke-width="24"/>
  </svg>
</section>

<section>
  <h2 class="abs serif section-title need-title">NAMIBIA NEED FOOD</h2>
  <p class="abs need-lead">Namibia is a young democracy in Sub-Saharan Africa with a population of approximately 2.5 Million people. The country's agricultural sector has been slow to keep up with the increasing population. As a consequence, approximately 60% of the food required to feed the nation is imported. The elevated cost of these imported foods means a large proportion of the population consume food with low nutritional value.</p>
  <p class="abs need-body">Despite vast tracts of available arable land and abundant water resources (both above and below ground), the agricultural sector has struggled to capitalise. This is largely due to a lack of invest ment, technical knowledge and available technologies.In conjunction with our various global partners, it is our aim for the “Harvest Crest Oruva” initiative to be a vector for an accelerated change in the food production landscape in Namibia which we believe will empower this beautiful country to become a self sufficient producer with food security at its foundation.</p>
  <div class="btn btn-tan" style="left:115px;top:1458px;width:157px;height:44px">Learn More</div>
  <div class="abs need-photo" role="img" aria-label="Farm workers harvesting sweet potatoes into crates beside a tractor"></div>
</section>

<section>
  <svg class="wave" style="top:1560px" height="202" viewBox="0 0 1200 202" aria-hidden="true">
    <path d="M0,140 C180,20 380,30 620,120 C860,208 1040,190 1200,120 L1200,202 L0,202 Z" fill="#c6a684"/>
    <path d="M0,140 C180,20 380,30 620,120 C860,208 1040,190 1200,120" fill="none" stroke="#c6a684" stroke-width="8" transform="translate(0,-16)"/>
    <path d="M40,108 C200,30 400,44 630,124 C850,196 1020,186 1160,126" fill="none" stroke="#0a6a3a" stroke-width="22"/>
  </svg>
  <div class="abs tan-band"></div>
  <div class="abs green-band"></div>
  <h2 class="abs serif section-title solution-title">THE HARVEST CREST SOLUTION</h2>

  <div class="card" style="left:100px">
    <div class="card-photo" role="img" aria-label="Farmer picking leafy greens into crates in a green field" style="background:linear-gradient(180deg,#5f9a3a,#3f7a2a 60%,#4a4a40)"></div>
    <div class="card-label">Primary Production Area</div>
  </div>
  <div class="card" style="left:620px">
    <div class="card-photo" role="img" aria-label="Two farmers with bananas and a tablet in a banana plantation" style="background:linear-gradient(180deg,#7a8a5a,#8a6a48 60%,#6a4a30)"></div>
    <div class="card-label">Empowerment Production Areas</div>
  </div>

  <h2 class="abs serif section-title fish-title">GIVE A MAN A FISH AND FEED HIM<br>FOR A DAY, TEACH A MAN TO FISH AND FEED<br>HIM FOR A LIFETIME</h2>
  <p class="abs fish-text">Education is key to empowerment and we embrace that concept. As such, we aim to offer a vocational education scheme for the participants in the Harvest Crest Oruva program. We aim to furnish the participants with the skills to be successful and sustainable farmers in their own rights</p>
  <div class="btn btn-tan" style="left:522px;top:2603px;width:157px;height:44px">Read More</div>
</section>

<section>
  <div class="abs about-photo" role="img" aria-label="Farmer reading a tablet among tall maize plants"></div>
  <h2 class="abs serif about-title">ABOUT US</h2>
  <p class="abs about-text">Lorem ipsum dolor sit amet, consectetur adipiscing elit, sed do eiusmod tempor incididunt ut labore et dolore magna aliqua. Ut enim ad minim veniam, quis nostrud exercitation ullamco laboris nisi ut aliquip ex ea commodo consequat. Duis aute irure dolor in reprehenderit in voluptate velit esse cillum dolore eu fugiat nulla pariatur. Excepteur sint occaecat cupidatat non proident, sunt in culpa qui officia deserunt mollit anim id est laborum. Ut enim ad minim veniam, quis nostrud exercitation ullamco laboris nisi ut aliquip ex ea commodo consequat. Duis aute irure dolor in reprehenderit in voluptate velit esse cillum dolore eu fugiat nulla pariatur. Excepteur sint occaecat cupidatat non proident, sunt in culpa qui officia deserunt mollit anim id est laborum.</p>
  <div class="btn btn-green" style="left:596px;top:3180px;width:157px;height:43px">Get Started</div>
</section>

<footer>
  <svg class="wave" style="top:3270px" height="132" viewBox="0 0 1200 132" aria-hidden="true">
    <path d="M0,90 C180,-6 380,10 620,80 C860,150 1040,130 1200,60 L1200,132 L0,132 Z" fill="#000"/>
    <path d="M0,84 C180,-12 380,4 620,74 C860,144 1040,124 1200,54" fill="none" stroke="#c6a684" stroke-width="10"/>
    <path d="M30,82 C200,10 400,24 630,90 C850,150 1030,140 1190,70" fill="none" stroke="#0a6a3a" stroke-width="22"/>
  </svg>
  <div class="abs footer-bg"></div>
  <h3 class="abs serif news-title">SIGN UP FOR NEWSLETTER</h3>
  <div class="abs news-field">
    <svg width="14" height="12" viewBox="0 0 14 12" aria-hidden="true"><rect x="1" y="1" width="12" height="10" rx="1" fill="none" stroke="#0a6a3a" stroke-width="1.3"/><path d="M1,2 L7,7 L13,2" fill="none" stroke="#0a6a3a" stroke-width="1.3"/></svg>
    <span>Enter Your Email</span>
  </div>
  <div class="btn btn-tan news-btn">Subscribe</div>
  <div class="abs rule"></div>

  <div class="abs footer-brand"><span class="brand-dot" style="width:18px;height:18px"></span><span>Harvest Crest Oruva</span></div>

  <div class="col-title" style="left:449px">CONTACT US</div>
  <div class="contact-item" style="top:3779px">
    <span class="icon-ring"><svg width="10" height="13" viewBox="0 0 10 13"><path d="M5,12 C2,8 1,6 1,4.5 A4,4 0 0 1 9,4.5 C9,6 8,8 5,12Z" fill="#fff"/><circle cx="5" cy="4.5" r="1.5" fill="#000"/></svg></span>
    <span>41, Lorem ipsum dolor sit<br>United States</span>
  </div>
  <div class="contact-item" style="top:3852px">
    <span class="icon-ring"><svg width="12" height="10" viewBox="0 0 12 10"><rect x="0.6" y="0.6" width="10.8" height="8.8" rx="1" fill="none" stroke="#fff" stroke-width="1.2"/><path d="M1,1.5 L6,5.5 L11,1.5" fill="none" stroke="#fff" stroke-width="1.2"/></svg></span>
    <span>hello@harvestcrest.example</span>
  </div>
  <div class="contact-item" style="top:3910px">
    <span class="icon-ring"><svg width="12" height="12" viewBox="0 0 12 12"><path d="M2.5,1 L4.5,1 L5.5,3.8 L4,5 C4.8,6.6 5.4,7.2 7,8 L8.2,6.5 L11,7.5 L11,9.5 C11,10.3 10.3,11 9.5,11 C5,10.7 1.3,7 1,2.5 C1,1.7 1.7,1 2.5,1Z" fill="#fff"/></svg></span>
    <span style="font-size:19px;font-weight:500">+1 555 014 2290</span>
  </div>

  <div class="col-title" style="left:758px">QUICK LINKS</div>
  <ul class="links" style="left:758px">
    <li>»<span>Home</span></li><li>»<span>About Us</span></li><li>»<span>Our Services</span></li><li>»<span>Reviews</span></li><li>»<span>Contact</span></li>
  </ul>
  <div class="col-title" style="left:951px">OTHER LINKS</div>
  <ul class="links" style="left:951px">
    <li>»<span>Contact Us</span></li><li>»<span>FAQ</span></li><li>»<span>Help Service</span></li><li>»<span>Terms Of Use</span></li><li>»<span>Privacy Policy</span></li>
  </ul>

  <div class="abs copyright">© 2024 HCO &nbsp;|&nbsp;&nbsp; All Rights Reserved &nbsp;&nbsp;|</div>
</footer>

</body>
</html>
```